Private Investment Firm Needs PowerPoint Presentation Template

Design PowerPoint template, take Pinebrook-submitted rough presentation draft, and drop it into new template. See attached Project Brief file for more detail.
Updates

Some decent designs have been submitted but they seem to lack the understanding of our target markets. I am hopeful that more time and feedback will result in better results.

Target Market(s)

Private company owners and intermediaries.

Font styles to use
Serif

Colors
3176b5

Requirements
Must have
• See attached Project Brief.
Nice to have
Should not have
• No B2C fluff--this is a B2B project.

```html
<!DOCTYPE html>
<html lang="en">
<head>
<meta charset="utf-8">
<title>Pinebrook Capital – Presentation Template Overview</title>
<link href="https://fonts.googleapis.com/css2?family=Arimo:wght@400;700&family=Tinos:wght@400;700&display=swap" rel="stylesheet">
<style>
:root{
  --blue:#3176b5;
  --blue-bright:#2a74c4;
  --blue-pale:#e6eff8;
  --grey-quote:#8a8a8a;
  --grey-row:#d4d4d4;
  --grey-box:#e9e9e9;
  --ink:#222;
  --board:#d6d6d6;
  --sans:'Arimo',Arial,sans-serif;
  --serif:'Tinos','Times New Roman',serif;
}
*{box-sizing:border-box;margin:0;padding:0}
html,body{width:1200px;height:686px;overflow:hidden;background:var(--board)}
.board{position:relative;width:1200px;height:686px}
.slide{position:absolute;width:236px;height:133px;background:#fff;overflow:hidden;font-family:var(--serif);color:var(--ink)}
.c1{left:3px}.c2{left:242px}.c3{left:481px}.c4{left:720px}.c5{left:959px}
.r1{top:3px}.r2{top:140px}.r3{top:277px}.r4{top:414px}.r5{top:551px}
.deco{position:absolute;right:0;top:0;width:62px;height:100%;background:linear-gradient(90deg,#fff,var(--blue-pale))}
.accent{position:absolute;left:6px;top:2px;width:4px;height:16px;background:var(--blue)}
.h{position:absolute;left:13px;top:12px;right:40px;font-family:var(--sans);font-weight:700;font-size:7.2px;line-height:1.05;color:var(--blue);text-transform:uppercase}
.foot{position:absolute;left:0;right:0;bottom:0;height:14px}
.foot .brand{position:absolute;left:6px;bottom:3px;font-family:var(--serif);font-size:5px;color:var(--blue)}
.foot .line{position:absolute;left:34px;right:17px;bottom:5px;height:2.5px;background:var(--blue)}
.foot .sq{position:absolute;right:6px;bottom:3px;width:8px;height:7px;background:var(--blue)}
.body{position:absolute;left:14px;right:18px;top:30px;font-size:4.3px;line-height:1.35}
.body ul{list-style:none}
.body li{padding-left:5px;position:relative;margin-bottom:1.6px}
.body li::before{content:"•";position:absolute;left:0}
.body li li{margin-left:6px}
.side{position:absolute;text-align:right;font-family:var(--sans);font-weight:700;text-transform:uppercase;font-size:7.2px;line-height:1.2}
.side .g{color:#777;font-weight:400}
.side .b{color:var(--blue)}
.photo{position:absolute;top:0;height:100%}
.brandmark{position:absolute;display:flex;align-items:center;gap:5px;font-family:var(--serif);font-weight:400;color:var(--blue);white-space:nowrap}
.brandmark .sqr{display:inline-block;background:var(--blue)}
.quote{position:absolute;inset:0;text-align:center;font-family:var(--sans);color:#fff}
.quote .mark{font-size:26px;font-weight:700;line-height:1;height:18px}
.quote p{font-size:5.3px;line-height:1.5;text-transform:uppercase;padding:0 24px}
.quote .who{font-size:6.5px;line-height:1.2;margin-top:2px}
.num{display:inline-block;width:8px;height:8px;border-radius:50%;background:var(--blue);color:#fff;font-family:var(--sans);font-size:5px;line-height:8px;text-align:center;position:absolute;left:-11px;top:0}
.uses{position:absolute;left:24px;right:16px;top:26px;font-family:var(--sans);font-size:3.4px;line-height:1.3}
.uses div{position:relative;margin-bottom:3.6px}
table{border-collapse:collapse;font-family:var(--sans)}
.section-band{position:absolute;left:0;width:236px;background:linear-gradient(180deg,#8fbfe6,#4a7aa8 60%,#234566)}
.ttl-box{position:absolute;right:0;bottom:0;background:#fff;padding:3px 4px 4px 8px;text-align:right;font-family:var(--sans);font-weight:700;font-size:8px;line-height:1.05}
</style>
</head>
<body>
<div class="board">

<!-- Row 1 -->
<section class="slide c1 r1">
  <div class="photo" style="left:100px;right:0;background:linear-gradient(160deg,#9cc6ea,#3e6f9d 55%,#1f3e61)" role="img" aria-label="Glass office towers seen from below against a blue sky"></div>
  <svg style="position:absolute;left:90px;top:0" width="146" height="133" aria-hidden="true"><polygon points="10,133 50,0 62,0 22,133" fill="#fff"/><polygon points="50,133 90,0 97,0 57,133" fill="var(--blue)" opacity=".85"/><polygon points="95,133 135,0 146,0 146,20 112,133" fill="#fff"/></svg>
  <div class="brandmark" style="left:7px;top:12px;font-size:10px"><span class="sqr" style="width:9px;height:9px"></span>Pinebrook Capital</div>
  <div style="position:absolute;left:6px;top:40px;width:4px;height:38px;background:var(--blue)"></div>
  <div style="position:absolute;left:12px;top:40px;font-family:var(--sans);font-size:9px;line-height:1.05;color:var(--blue)">INTRODUCTION<br>TO<br>NON-CONTROL<br>CAPITAL</div>
  <div style="position:absolute;left:8px;top:82px;width:80px;font-family:var(--sans);font-size:4px;line-height:1.3">The Lower Middle Market Private Company Strategy for Raising Capital While Maintaining Business Control</div>
  <div style="position:absolute;left:6px;bottom:5px;font-size:4px;font-weight:700">Fall 2018</div>
</section>

<section class="slide c2 r1">
  <div class="photo" style="left:100px;right:0;background:radial-gradient(circle at 55% 50%,#cfe3f6,#5a88b6 45%,#142c48)" role="img" aria-label="Hand touching a glowing network of digital business icons"></div>
  <svg style="position:absolute;left:90px;top:0" width="146" height="133" aria-hidden="true"><polygon points="10,133 50,0 62,0 22,133" fill="#fff"/><polygon points="50,133 90,0 97,0 57,133" fill="var(--blue)" opacity=".85"/><polygon points="95,133 135,0 146,0 146,20 112,133" fill="#fff"/></svg>
  <div class="brandmark" style="left:7px;top:12px;font-size:10px"><span class="sqr" style="width:9px;height:9px"></span>Pinebrook Capital</div>
  <div style="position:absolute;left:6px;top:40px;width:4px;height:38px;background:#999"></div>
  <div style="position:absolute;left:12px;top:40px;font-family:var(--sans);font-size:9px;line-height:1.05;color:#777">INTRODUCTION<br>TO<br>NON-CONTROL<br>CAPITAL</div>
  <div style="position:absolute;left:8px;top:82px;width:80px;font-family:var(--sans);font-size:4px;line-height:1.3">The Lower Middle Market Private Company Strategy for Raising Capital While Maintaining Business Control</div>
  <div style="position:absolute;left:6px;bottom:5px;font-size:4px;font-weight:700">Fall 2018</div>
</section>

<section class="slide c3 r1">
  <div class="deco"></div><div class="accent"></div>
  <h2 class="h">Introduction</h2>
  <div class="body" style="top:27px;right:40px">
    <ul>
      <li>Private company owners have traditionally considered two capital raising options:
        <ul><li>Borrow from a local bank, or</li><li>Sell most or all of the company to a change-of-control investor (aka Buyout firm)</li></ul></li>
      <li>An alternative most have not considered is the raising of Non-Control Capital, or capital that is invested into the business yet allows those same owners to retain controlling interest in their company</li>
      <li>Non-Control Capital is not appropriate for every private company owner but neither is a Change-of-Control sale</li>
      <li>The key is to determine what the business and owners require, and then partner with an investor best aligned with those needs so that long-term company growth, and personal goals, can both be achieved</li>
    </ul>
  </div>
  <div class="foot"><span class="brand">Pinebrook</span><span class="line"></span><span class="sq"></span></div>
</section>

<section class="slide c4 r1">
  <div class="deco"></div><div class="accent"></div>
  <h2 class="h" style="top:12px">What is Non-Control Capital?</h2>
  <div style="position:absolute;left:14px;right:18px;top:21px;font-family:var(--sans);font-size:3.3px;line-height:1.35">
    • Non-Control Capital is an investment which is primarily used for the ongoing operation and/or growth of a business but <u>also</u> allows the current owners to retain:<br>
    &nbsp;&nbsp;✓ Control of the business economics &nbsp;&nbsp; ✓ Control of strategy and key decision making<br>
    &nbsp;&nbsp;✓ Control of the business operations &nbsp;&nbsp; ✓ Control of the Board of Directors<br>
    • Requires the alignment of management incentives with ownership<br>
    • In essence, a company receives the capital it needs to implement its business plans but owners continue to retain ultimate control
  </div>
  <div style="position:absolute;right:16px;top:56px;font-family:var(--sans);font-weight:700;font-size:7px;color:var(--blue);text-align:right">WHEN IS A</div>
  <div style="position:absolute;left:14px;top:64px;font-family:var(--sans);font-weight:700;font-size:7px;color:var(--blue)">NON-CONTROL TRANSACTION APPROPRIATE?</div>
  <div style="position:absolute;left:14px;right:18px;top:72px;font-family:var(--sans);font-size:3.3px;line-height:1.35">
    The company has opportunities to expand but requires capital to do so<br>At least one active owner <u>is not</u> close to retirement<br>The company is not in a turnaround situation<br>Family members may work in the business and want to continue<br>Owners care about keeping the business in their family name (legacy)<br>Liquidity (dividend) is not the major use of the invested capital<br>Owners are sensitive to utilizing too much debt<br>Companies require more than just capital:<br>They may also need operational, marketing, financial, and/or technology counsel
  </div>
  <div class="foot"><span class="brand">Pinebrook</span><span class="line"></span><span class="sq"></span></div>
</section>

<section class="slide c5 r1" style="background:var(--blue-bright)">
  <div class="quote" style="top:8px">
    <div class="mark">“</div>
    <p>Our company had several business opportunities but I needed outside capital to take advantage of them. Why would I cede control of my business when we were at the exact point when raising outside capital would allow me to accelerate growth and achieve my life-long business and personal goals?!</p>
    <div class="mark" style="margin-top:2px">”</div>
    <div class="who"><b>Mark Ellison</b><br>CEO<br>The Ridgeline Group</div>
  </div>
</section>

<!-- Row 2 -->
<section class="slide c1 r2" style="background:var(--grey-quote)">
  <div class="quote" style="top:8px">
    <div class="mark">“</div>
    <p>Our company had several business opportunities but I needed outside capital to take advantage of them. Why would I cede control of my business when we were at the exact point when raising outside capital would allow me to accelerate growth and achieve my life-long business and personal goals?!</p>
    <div class="mark" style="margin-top:2px">”</div>
    <div class="who" style="color:#111"><b>Mark Ellison</b><br>CEO<br>The Ridgeline Group</div>
  </div>
</section>

<section class="slide c2 r2">
  <div class="deco"></div><div class="accent"></div>
  <h2 class="h" style="top:6px">The 12 Primary Uses of Non-Control Capital</h2>
  <div class="uses">
    <div><span class="num">1</span><b>Growth:</b> used to organically expand a business: introduce new products, build a new factory, hire additional management or employees, enter new markets, or for general working capital purposes</div>
    <div><span class="num">2</span><b>Acquisitions:</b> Capital used to acquire one or more competitors or to allow for further vertical or horizontal integration</div>
    <div><span class="num">3</span><b>Partner or Shareholder Buy-Out:</b> Capital used to buy-out an inactive or retiring partner or shareholder</div>
    <div><span class="num">4</span><b>Management Buy-Out (MBO):</b> When the incumbent management team buys most or all of the ownership of an inactive founder or executive</div>
    <div><span class="num">5</span><b>Management Buy-In (MBI):</b> When an external, experienced executive buys a business from one or more inactive owners and needs additional capital to affect the purchase</div>
    <div><span class="num">6</span><b>Family Ownership &amp; Wealth Transfer:</b> When junior generations of a family acquire most or all of the ownership interests of more senior generations allowing the business to remain in the family name</div>
  </div>
  <div class="foot"><span class="brand">Pinebrook</span><span class="line"></span><span class="sq"></span></div>
</section>

<section class="slide c3 r2">
  <div class="deco"></div><div class="accent"></div>
  <h2 class="h" style="top:6px">The 12 Primary Uses of Non-Control Capital</h2>
  <div class="uses">
    <div><span class="num">7</span><b>Balance Sheet Recapitalization:</b> Changes the debt and equity mixture of a Company's finances to a more optimal capital structure</div>
    <div><span class="num">8</span><b>Refinancing:</b> Replacing one form or type of debt with another with better terms, conditions, and flexibility</div>
    <div><span class="num">9</span><b>Family Office Support:</b> Allows a Family Office to affect an investment in a Company by allowing a junior capital provider to invest alongside them</div>
    <div><span class="num">10</span><b>Senior Lender Enhancement or Transition:</b> When a Company has grown beyond the means or interest of its senior bank but needs additional capital to support its continuing growth</div>
    <div><span class="num">11</span><b>De-Lever Balance Sheet:</b> When a Company has taken on too much debt (typically senior debt) and replaces some of it with other equity or other junior capital to provide operating flexibility</div>
    <div><span class="num">12</span><b>Owner Dividend (Liquidity):</b> When one or more owners take a non-life changing cash distribution, typically used to diversify their net worth</div>
  </div>
  <div class="foot"><span class="brand">Pinebrook</span><span class="line"></span><span class="sq"></span></div>
</section>

<section class="slide c4 r2">
  <div class="deco"></div><div class="accent"></div>
  <h2 class="h" style="top:22px">Pinebrook Provides Junior Capital</h2>
  <div style="position:absolute;left:12px;right:16px;top:34px;height:6px;background:var(--blue);color:#fff;font-family:var(--sans);font-weight:700;font-size:3.8px;text-align:center;line-height:6px">BALANCE SHEET SENIORITY / CAPITAL STACK HIERARCHY</div>
  <div style="position:absolute;left:12px;top:41px;width:58px;font-family:var(--sans);font-size:3.4px;line-height:6.8px">
    <div style="background:#bbb;font-weight:700;padding-left:1px">Senior Debt</div>
    <div style="background:var(--grey-row);padding-left:10px">Revolver</div>
    <div style="background:var(--grey-row);padding-left:10px">Asset-Based Loan</div>
    <div style="background:var(--grey-row);padding-left:10px">Senior Term Loan</div>
    <div style="background:#bbb;font-weight:700;padding-left:1px">Combination</div>
    <div style="background:var(--grey-row);padding-left:10px">Unitranche</div>
    <div style="background:#bbb;font-weight:700;padding-left:1px">Junior Capital</div>
    <div style="background:var(--grey-row);padding-left:10px">Subordinated Debt</div>
    <div style="background:var(--grey-row);padding-left:10px">Preferred Stock</div>
    <div style="background:var(--grey-row);padding-left:10px">Common Stock</div>
  </div>
  <div style="position:absolute;left:71px;right:16px;top:41px;height:40px;background:var(--grey-box);font-family:var(--sans);text-align:center;padding:10px 4px 0;font-size:3.4px;line-height:1.3"><b style="font-size:4.6px">Senior Debt Capital Providers</b><br>Paid back first, plays more of a lender than partner role, less value-added, less equity dilutive, less expensive capital, but not strategically focused</div>
  <div style="position:absolute;left:71px;right:16px;top:82px;height:27px;background:var(--grey-box);font-family:var(--sans);text-align:center;padding:2px 4px 0;font-size:3.4px;line-height:1.3"><b style="font-size:4.6px">What Pinebrook Invests</b><br>Sits junior to all other capital (taking on more risk), plays a partner role, more value-added services provided, more expensive than senior debt, but supplies an engine for continuous improvement and growth</div>
  <div class="foot"><span class="brand">Pinebrook</span><span class="line"></span><span class="sq"></span></div>
</section>

<section class="slide c5 r2">
  <div class="deco"></div><div class="accent"></div>
  <h2 class="h" style="top:14px;line-height:1.15">Balance Sheet<br><span style="font-size:6.2px">Pinebrook's Position in the Capital Stack</span></h2>
  <div style="position:absolute;left:6px;top:35px;width:86px;font-family:var(--sans);font-size:3.4px;line-height:6.8px">
    <div style="background:var(--blue);color:#fff;font-weight:700;padding-left:2px">ASSETS</div>
    <div style="padding-left:2px">Cash</div><div style="padding-left:2px">Marketable Securities</div><div style="padding-left:2px">Accounts Receivable</div><div style="padding-left:2px">Inventory</div><div style="padding-left:2px">PP&amp;E</div><div style="padding-left:2px">Intangible Assets</div><div style="padding-left:2px">Other Assets</div>
  </div>
  <div style="position:absolute;left:100px;top:35px;width:86px;font-family:var(--sans);font-size:3.4px;line-height:6.8px">
    <div style="background:var(--blue);color:#fff;font-weight:700;padding-left:2px">LIABILITIES</div>
    <div style="padding-left:2px">Accounts Payable</div><div style="padding-left:2px">Taxes Payable</div><div style="padding-left:2px">Revolver</div><div style="padding-left:2px">Senior Term Loan</div><div style="padding-left:2px">Unitranche Debt</div><div style="padding-left:2px">Subordinated Debt*</div>
    <div style="background:var(--blue);color:#fff;font-weight:700;padding-left:2px">EQUITY</div>
    <div style="padding-left:2px">Owners' Equity</div><div style="padding-left:2px">Preferred Stock*</div><div style="padding-left:2px">Common Stock*</div>
  </div>
  <div style="position:absolute;right:14px;top:118px;font-size:3.4px">*Key: Where Pinebrook Participates</div>
  <div class="foot"><span class="brand">Pinebrook</span></div>
</section>

<!-- Row 3 -->
<section class="slide c1 r3">
  <div class="section-band" style="top:0;height:30px" role="img" aria-label="Mirrored skyscraper facades against blue sky"></div>
  <div class="section-band" style="top:92px;height:41px" role="img" aria-label="Glass tower facades seen from below"></div>
  <div class="brandmark" style="left:50px;top:52px;font-size:15px"><span class="sqr" style="width:13px;height:13px"></span>Pinebrook Capital</div>
  <div class="ttl-box">FIRM<br>OVERVIEW</div>
</section>

<section class="slide c2 r3">
  <div class="deco"></div><div class="accent" style="top:8px"></div>
  <h2 class="h" style="top:20px">Pinebrook Capital Introduction</h2>
  <div class="body" style="top:29px;font-size:4.6px">
    <ul>
      <li>Pinebrook invests Non-Control Capital direct with management
        <ul><li>Owners retain control of their business after we invest</li><li>Without a traditional Change-of-Control private equity sponsor</li></ul></li>
      <li>One of the longest-standing junior capital funds targeting the lower middle market</li>
      <li>Since 1994, Pinebrook has completed 74 (and counting) Non-Control Capital investments and managed over $600 million</li>
      <li>Our interests are aligned with management or we don't invest</li>
      <li>"Consultants with Capital"
        <ul><li>We partner with companies that seek capital <b><u>and</u></b> our assistance to improve and/or grow the business</li></ul></li>
    </ul>
  </div>
  <div class="foot"><span class="brand">Pinebrook</span><span class="line"></span><span class="sq"></span></div>
</section>

<section class="slide c3 r3">
  <div class="deco"></div><div class="accent" style="top:0;height:18px"></div>
  <h2 class="h" style="top:18px">Overview</h2>
  <div class="side" style="left:6px;width:64px;top:31px"><span class="b">We have over</span><br><span class="g">140 years</span><br><span class="b">of combined principal investing experience</span></div>
  <div class="body" style="left:74px;right:18px;top:31px;font-size:4.6px;line-height:1.55">
    <ul>
      <li>Offices in Boston and San Francisco with 12 investment professionals <b><u>fully dedicated</u></b> to Non-Control Capital investing</li>
      <li>Invest combinations of equity and subordinated debt securities</li>
      <li>Currently investing $260MM fourth fund
        <ul><li>9 Fund IV investments made to date (as of November 1, 2018)</li><li>Over $120MM of "dry powder" available for new investments</li></ul></li>
    </ul>
  </div>
  <div class="foot"><span class="brand">Pinebrook</span><span class="line"></span><span class="sq"></span></div>
</section>

<section class="slide c4 r3">
  <div class="deco"></div><div class="accent" style="top:0;height:18px"></div>
  <h2 class="h" style="top:18px">What We Do / And Why</h2>
  <div class="side" style="left:6px;width:74px;top:54px"><span class="g">Non-Control</span><br><span class="b">Capital transactions only</span></div>
  <div class="body" style="left:82px;right:18px;top:45px;font-size:4.6px;line-height:1.55">
    <ul>
      <li>Companies looking for a partner to help them grow, not sellers looking to exit</li>
      <li>Management's personal wealth directly tied to the performance of the investment</li>
      <li>Situational investors with a generalist approach</li>
      <li>Our heritage reflects decades of Non-Control Capital investing—it's all we do</li>
    </ul>
  </div>
  <div class="foot"><span class="brand">Pinebrook</span><span class="line"></span><span class="sq"></span></div>
</section>

<section class="slide c5 r3">
  <div class="deco"></div><div class="accent" style="top:10px"></div>
  <h2 class="h" style="top:12px">Pinebrook Representative Non-Control Capital Investments</h2>
  <div style="position:absolute;left:6px;top:34px;width:36px;font-family:var(--sans);font-size:4px;font-weight:700;color:var(--blue)">Aerolite Flight Group</div>
  <div style="position:absolute;left:46px;right:16px;top:30px;font-size:2.9px;line-height:1.3">• Operates dedicated commercial airline pilot training facilities with classrooms, procedures trainers and flight simulators.<br><span style="color:var(--blue)">• Pinebrook's capital was used to fund the Company's near-to-intermediate-term growth and new training centers.</span></div>
  <div style="position:absolute;right:18px;top:56px;width:30px;height:11px;background:#111"></div>
  <div style="position:absolute;left:6px;right:54px;top:52px;font-size:2.9px;line-height:1.3">• Manufacturer of vibration isolation, seismic control and shock protection products for critical equipment.<br><span style="color:var(--blue)">• Pinebrook's capital was used to acquire two attractive tuck-in companies, improving The Ridgeline Group's competitive position.</span></div>
  <div style="position:absolute;left:6px;top:97px;width:30px;font-family:var(--sans);font-size:4px;font-weight:700;color:var(--blue)">Summit Alert</div>
  <div style="position:absolute;left:40px;right:16px;top:80px;font-size:2.9px;line-height:1.3">• Provider of fire and security alarm design, installation, service and monitoring for commercial and residential end-markets.<br><span style="color:var(--blue)">• Pinebrook's capital was used to give the CEO room to strategically grow the business. The Company and Pinebrook grew it substantially, and the next generation of family management now owns a larger stake than five years earlier.</span></div>
  <div class="foot"><span class="brand">Pinebrook</span><span class="line"></span><span class="sq"></span></div>
</section>

<!-- Row 4 -->
<section class="slide c1 r4">
  <div class="deco"></div><div class="accent" style="top:0;height:18px"></div>
  <h2 class="h" style="top:12px;right:60px">Pinebrook Representative Non-Control Capital Investments</h2>
  <div style="position:absolute;left:8px;top:40px;width:56px;font-family:var(--sans);font-size:5px;font-weight:700;color:var(--blue)">Harlow Consulting</div>
  <div style="position:absolute;left:66px;right:40px;top:34px;font-size:2.9px;line-height:1.3">• Provider of audit compliance software and consulting services for hospitals and physician practices.<br><span style="color:var(--blue)">• Pinebrook's capital was used to assist the active CEO in acquiring the business from an inactive founder and in a key software investment.</span></div>
  <div style="position:absolute;left:6px;right:90px;top:60px;font-size:2.9px;line-height:1.3">• Provider of third-party vehicle maintenance services for private, public and for-hire fleet-based businesses nationwide.<br><span style="color:var(--blue)">• Pinebrook's capital was used to support the Company's accelerating growth. Pinebrook provided subordinated debt and preferred stock.</span></div>
  <div style="position:absolute;left:152px;top:64px;width:40px;font-family:var(--sans);font-size:5px;font-weight:700;color:var(--blue)">Fleetwell Services</div>
  <div style="position:absolute;left:8px;top:92px;width:48px;font-family:var(--sans);font-size:5px;font-weight:700;color:var(--blue)">Vesta Packaging</div>
  <div style="position:absolute;left:58px;right:40px;top:88px;font-size:2.9px;line-height:1.3">• Provides comprehensive and custom packaging for liquid home cleaning products.<br><span style="color:var(--blue)">• Pinebrook's capital was used to assist a family office in acquiring the Company as part of its growth strategy.</span></div>
  <div class="foot"><span class="brand">Pinebrook</span><span class="line"></span><span class="sq"></span></div>
</section>

<section class="slide c2 r4">
  <div class="deco"></div><div class="accent" style="top:0;height:18px"></div>
  <h2 class="h" style="top:18px">Investment Criteria</h2>
  <div class="side" style="left:6px;width:64px;top:42px"><span class="g">Pinebrook invests in</span><br><span class="b">established, lower middle market companies</span></div>
  <div class="body" style="left:76px;right:14px;top:40px;font-size:4.6px;line-height:1.55">
    <ul>
      <li>Revenues of $10MM to $150MM</li>
      <li>EBITDA of at least $2MM</li>
      <li>Pinebrook investment size of $5MM to $25MM</li>
      <li>Experienced, committed, and incented management</li>
      <li>Limited leverage (asset values "ahead" of Pinebrook)</li>
      <li>Niche market leader with differentiated services or products</li>
      <li>Focused on value-added execution, not proof of concept</li>
    </ul>
  </div>
  <div class="foot"><span class="brand">Pinebrook</span><span class="line"></span><span class="sq"></span></div>
</section>

<section class="slide c3 r4">
  <div class="deco"></div><div class="accent" style="top:0;height:18px"></div>
  <h2 class="h" style="top:18px">Consultants with Capital</h2>
  <div class="side" style="left:6px;width:56px;top:42px"><span class="g">We help</span><br><span class="b">portfolio companies create greater value.</span></div>
  <div class="body" style="left:62px;right:16px;top:33px;font-size:4.4px;line-height:1.55">
    <ul>
      <li>Facilitate strategy development</li>
      <li>Improve financial reporting and information systems</li>
      <li>Assist with key hires, such as CFOs and COOs, if needed</li>
      <li>Source, evaluate, finance, close, and integrate acquisitions</li>
      <li>Invest additional capital</li>
      <li>Annual Executive Summit focused on professional development and networking</li>
      <li>Most importantly, act as a sounding board to help solve problems, identify new opportunities, and create value</li>
      <li>We personally invest in every transaction</li>
    </ul>
  </div>
  <div style="position:absolute;right:10px;top:110px;width:130px;text-align:right;font-family:var(--sans);font-size:3.2px;color:var(--blue)">These options are made available to our portfolio companies, if needed, and not forced upon them</div>
  <div class="foot"><span class="brand">Pinebrook</span><span class="line"></span><span class="sq"></span></div>
</section>

<section class="slide c4 r4">
  <div class="deco"></div><div class="accent" style="top:0;height:18px"></div>
  <h2 class="h" style="top:18px">Pinebrook Impact - By the Numbers</h2>
  <div class="side" style="left:6px;width:64px;top:33px"><span class="g">During Pinebrook's average investment term,</span><br><span class="b">our impact has been noteworthy</span></div>
  <table style="position:absolute;left:68px;top:44px;width:116px;font-size:3.3px">
    <tr style="background:var(--blue);color:#fff;font-weight:700;height:10px"><td style="padding-left:2px">Impact Category</td><td style="text-align:center">Actual<br>Impact</td><td style="text-align:center">Min/Max*<br>Removed</td></tr>
    <tr style="background:#eef2f7;height:6.5px"><td style="padding-left:2px">Average Revenue Growth</td><td style="text-align:center">113%</td><td style="text-align:center">91%</td></tr>
    <tr style="background:#dce5f0;height:6.5px"><td style="padding-left:2px">Average EBITDA Growth</td><td style="text-align:center">75%</td><td style="text-align:center">78%</td></tr>
    <tr style="background:#eef2f7;height:6.5px"><td style="padding-left:2px">Average Employee Growth</td><td style="text-align:center">213%</td><td style="text-align:center">49%</td></tr>
  </table>
  <div style="position:absolute;left:68px;top:86px;width:80px;font-size:3.2px;line-height:1.3;color:var(--blue)">*Note: Actual Impact figures based on 55 exited investments from 1994 to 2017. Min/Max removed from each of 3 fully invested funds.</div>
  <div class="foot"><span class="brand">Pinebrook</span><span class="line"></span><span class="sq"></span></div>
</section>

<section class="slide c5 r4">
  <div class="deco"></div><div class="accent" style="top:0;height:18px"></div>
  <h2 class="h" style="top:18px">In Summary</h2>
  <div class="body" style="top:30px;font-size:4.3px">
    <ul>
      <li>There is an alternative to giving up control of your company through an infusion of Non-Control Capital</li>
      <li>All investors are not created equal</li>
      <li>Non-Control Capital investing is a specialty:
        <ul><li>Choose only an investor with decades of Non-Control heritage, experience, and focus (see <span style="color:var(--blue)">Questionnaire in the Epilogue section of this presentation</span>)</li></ul></li>
      <li>It means more than just capital:
        <ul><li>Team up with an accomplished investor who can bring demonstrated growth abilities, not simply write a check</li></ul></li>
      <li>Chemistry between company management and the investor is critical:
        <ul><li>If Pinebrook's interests are not aligned with management, we don't invest</li></ul></li>
    </ul>
  </div>
  <div class="foot"><span class="brand">Pinebrook</span><span class="line"></span><span class="sq"></span></div>
</section>

<!-- Row 5 -->
<section class="slide c1 r5">
  <div class="section-band" style="top:0;height:30px" role="img" aria-label="Mirrored skyscraper facades against blue sky"></div>
  <div class="section-band" style="top:92px;height:41px" role="img" aria-label="Glass tower facades seen from below"></div>
  <div class="brandmark" style="left:50px;top:52px;font-size:15px"><span class="sqr" style="width:13px;height:13px"></span>Pinebrook Capital</div>
  <div class="ttl-box">EPILOGUE</div>
</section>

<section class="slide c2 r5">
  <div class="deco"></div><div class="accent" style="top:6px"></div>
  <h2 class="h" style="top:5px;right:50px">The Critical Questions to Ask of Any Prospective Non-Control Investor</h2>
  <div style="position:absolute;left:13px;right:16px;top:22px;font-family:var(--sans);font-size:3px;line-height:1.3;color:#666">Non-Control Capital is a specialty, so only those firms with deep experience investing it as a team should be considered <span style="float:right">Non-Control Capital Questionnaire</span></div>
  <div style="position:absolute;left:6px;top:32px;font-family:var(--sans);font-weight:700;font-size:8px;line-height:13px;color:var(--blue)">?<br>?<br>?<br>?<br>?<br>?</div>
  <div class="uses" style="left:15px;top:33px;font-size:2.9px;line-height:1.25">
    <div><b>Question #1: How many years has the firm been investing Non-Control Capital?</b><br><span style="color:var(--blue)">Best Answer:</span> 5+ years investing as a team within the current firm. Indicates comfort and experience working together.</div>
    <div><b>Question #2: How many fully-invested Non-Control Capital funds in the firm's history?</b><br><span style="color:var(--blue)">Best Answer:</span> 2+ fully-invested funds. Indicates experience and ability to close deals with the current regime.</div>
    <div><b>Question #3: What percentage of the firm's voting investment committee are full-time Non-Control Capital investors?</b><br><span style="color:var(--blue)">Best Answer:</span> Super-majority. Indicates commitment and focus on NCC.</div>
    <div><b>Question #4: What is the number of Non-Control Capital investments made with the current firm and team?</b><br><span style="color:var(--blue)">Best Answer:</span> 20+. Indicates long-term experience and comfort with current team.</div>
    <div><b>Question #5: What percentage of portfolio investments made are "sponsorless"?</b><br><span style="color:var(--blue)">Best Answer:</span> 80%+ of all investments closed in the last 5 years. Indicates ability to add value as a sole minority investor.</div>
    <div><b>Question #6: Can the investor show quantifiable proof of their ability to assist portfolio companies with growth and improvement?</b><br><span style="color:var(--blue)">Best Answer:</span> Yes. Owners should evaluate investors on actual historical revenue, EBITDA and employee growth impact.</div>
  </div>
  <div class="foot"><span class="brand">Pinebrook</span><span class="line"></span><span class="sq"></span></div>
</section>

<section class="slide c3 r5">
  <div class="deco"></div><div class="accent" style="top:6px"></div>
  <h2 class="h" style="top:5px;right:50px">The Critical Questions to Ask of Any Prospective Non-Control Investor</h2>
  <div style="position:absolute;left:13px;right:16px;top:22px;font-family:var(--sans);font-size:3px;line-height:1.3;color:#666">Non-Control Capital is a specialty, so only those firms with deep experience investing it as a team should be considered <span style="float:right">Non-Control Capital Questionnaire</span></div>
  <div style="position:absolute;left:9px;top:33px;width:1.5px;height:76px;background:var(--blue)"></div>
  <div class="uses" style="left:13px;top:33px;font-size:2.9px;line-height:1.25">
    <div><b>Question #1: How many years has the firm been investing Non-Control Capital?</b><br><span style="color:var(--blue)">Best Answer:</span> 5+ years investing as a team within the current firm. Indicates comfort and experience working together.</div>
    <div><b>Question #2: How many fully-invested Non-Control Capital funds in the firm's history?</b><br><span style="color:var(--blue)">Best Answer:</span> 2+ fully-invested funds. Indicates experience and ability to close deals with the current regime.</div>
    <div><b>Question #3: What percentage of the firm's voting investment committee are full-time Non-Control Capital investors?</b><br><span style="color:var(--blue)">Best Answer:</span> Super-majority. Indicates commitment and focus on NCC.</div>
    <div><b>Question #4: What is the number of Non-Control Capital investments made with the current firm and team?</b><br><span style="color:var(--blue)">Best Answer:</span> 20+. Indicates long-term experience and comfort with current team.</div>
    <div><b>Question #5: What percentage of portfolio investments made are "sponsorless"?</b><br><span style="color:var(--blue)">Best Answer:</span> 80%+ of all investments closed in the last 5 years. Indicates ability to add value as a sole minority investor.</div>
    <div><b>Question #6: Can the investor show quantifiable proof of their ability to assist portfolio companies with growth and improvement?</b><br><span style="color:var(--blue)">Best Answer:</span> Yes. Owners should evaluate investors on actual historical revenue, EBITDA and employee growth impact.</div>
  </div>
  <div class="foot"><span class="brand">Pinebrook</span><span class="line"></span><span class="sq"></span></div>
</section>

<section class="slide c4 r5">
  <div class="photo" style="left:120px;right:0;background:linear-gradient(180deg,#f4f7fb,#dbe6f2)"></div>
  <div style="position:absolute;left:148px;top:18px;width:70px;height:112px;border-radius:30px 30px 4px 4px;background:linear-gradient(180deg,#8c96a3,#2c3440)" role="img" aria-label="Portrait photo of the firm principal in a dark suit"></div>
  <div class="accent" style="top:8px"></div>
  <h2 class="h" style="top:14px">Contact</h2>
  <div style="position:absolute;left:13px;top:25px;font-size:4.2px;line-height:1.4">
    <span style="color:var(--blue)">PINEBROOKCAPITAL.COM</span><br><br>
    <b style="color:var(--blue);font-size:5px">DANIEL R. MERCER</b><br>Principal<br>41 Alder Ridge Road, Suite 210<br>Brookfield, CT 06804<br>Direct: (555) 014-2201<br><u style="color:var(--blue)">dmercer@pinebrookcapital.com</u>
  </div>
  <div style="position:absolute;left:13px;top:87px;font-size:3.6px;line-height:1.35"><b style="color:var(--blue)">BOSTON OFFICE</b><br>12 Harbor Lane, Suite 300<br>Salem, MA 01970<br>(555) 014-2200</div>
  <div style="position:absolute;left:70px;top:87px;font-size:3.6px;line-height:1.35"><b style="color:var(--blue)">SAN FRANCISCO OFFICE</b><br>200 Market Court, Suite 410<br>San Francisco, CA 94105<br>(555) 014-2300</div>
  <div style="position:absolute;left:42px;bottom:4px;font-size:2.8px">Copyright © 2018 • Pinebrook Capital Partners • All Rights Reserved</div>
  <div class="foot"><span class="brand">Pinebrook</span></div>
</section>

<section class="slide c5 r5">
  <div class="photo" style="left:100px;right:0;background:linear-gradient(90deg,#fff,#e4eef8)"></div>
  <div style="position:absolute;left:142px;top:14px;width:80px;height:119px;border-radius:34px 34px 0 0;background:linear-gradient(180deg,#8c96a3,#2c3440)" role="img" aria-label="Portrait photo of the firm principal in a dark suit"></div>
  <div class="accent" style="top:8px"></div>
  <h2 class="h" style="top:14px">Contact</h2>
  <div style="position:absolute;left:13px;top:25px;font-size:4.2px;line-height:1.4">
    <span style="color:var(--blue)">PINEBROOKCAPITAL.COM</span><br><br>
    <b style="color:var(--blue);font-size:5px">DANIEL R. MERCER</b><br>Principal<br>41 Alder Ridge Road, Suite 210<br>Brookfield, CT 06804<br>Direct: (555) 014-2201<br><u style="color:var(--blue)">dmercer@pinebrookcapital.com</u>
  </div>
  <div style="position:absolute;left:13px;top:92px;font-size:3.6px;line-height:1.35"><b style="color:var(--blue)">BOSTON OFFICE</b><br>12 Harbor Lane, Suite 300<br>Salem, MA 01970<br>(555) 014-2200</div>
  <div style="position:absolute;left:70px;top:92px;font-size:3.6px;line-height:1.35"><b style="color:var(--blue)">SAN FRANCISCO OFFICE</b><br>200 Market Court, Suite 410<br>San Francisco, CA 94105<br>(555) 014-2300</div>
  <div style="position:absolute;left:42px;bottom:4px;font-size:2.8px">Copyright © 2018 • Pinebrook Capital Partners • All Rights Reserved</div>
  <div class="foot"><span class="brand">Pinebrook</span></div>
</section>

</div>
</body>
</html>
```